Transform Your Giving

I need a tri-fold brochure that will fit in a standard number 10 business envelope. Meadowlark and Allied Services is a charitable nonprofit. The goal of this brochure is to stimulate people into thinking about other ways to make a donation. The design should communicate the essential information on donation options, create a sense of professional integrity, be graphically sharp, easy to read and laid out in a way that doesn't make the material appear crowded.

```html
<!DOCTYPE html>
<html lang="en">
<head>
<meta charset="utf-8">
<title>Transform Your Giving – Meadowlark and Allied Services brochure</title>
<link href="https://fonts.googleapis.com/css2?family=Titillium+Web:ital,wght@0,400;0,600;0,700;1,700&family=Source+Sans+3:wght@400;600&family=Montserrat:wght@400;500&display=swap" rel="stylesheet">
<style>
:root{
  --navy:#231c6e;
  --indigo:#2d2484;
  --green:#3cb83a;
  --ink:#2b2b2b;
  --paper:#ffffff;
  --backdrop:#7b7b7b;
  --mark-grey:#b9b9bd;
}
*{box-sizing:border-box;margin:0;padding:0}
html,body{width:1096px;height:1200px;overflow:hidden;background:var(--backdrop)}
body{font-family:"Source Sans 3",sans-serif;color:var(--ink)}
.stage{position:absolute;left:0;top:0;width:1841px;height:2016px;transform:scale(0.5953);transform-origin:0 0}
.sheet{position:absolute;left:344px;width:1154px;height:866px;background:var(--paper);display:flex}
.sheet--outside{top:106px}
.sheet--inside{top:1044px}
.panel{position:relative;width:384.67px;height:100%;overflow:hidden}
.sheet--inside .panel{background:linear-gradient(90deg,#fff 0%,#fff 86%,#ececec 100%)}
.sheet--inside .panel:nth-child(2){background:linear-gradient(90deg,#f1f1f1 0%,#fff 8%,#fff 90%,#ececec 100%)}
.sheet--inside .panel:nth-child(3){background:linear-gradient(90deg,#efefef 0%,#fff 8%)}
.abs{position:absolute}
.photo{position:absolute;left:0;width:100%}
.curve{position:absolute;left:0;width:100%}
h2,h3,.head{font-family:"Titillium Web",sans-serif;color:var(--navy);font-weight:700}
.section-title{font-size:21px;letter-spacing:.2px}
.lead{font-size:18px;line-height:21.7px;color:#222}
.body{font-size:15.3px;line-height:18.3px;color:#2a2a2a}
.how{font-size:18px;line-height:20px}
.item-title{font-size:15.8px;line-height:19.5px;font-weight:700}
.item-tag{font-family:"Titillium Web",sans-serif;font-weight:700;font-style:italic;color:var(--green);font-size:15.6px;line-height:19px}
.icon{position:absolute;width:70px;height:70px}
.icon--ring{width:86px;height:86px}
.label{position:absolute;font-family:"Titillium Web",sans-serif;font-weight:700;color:var(--ink);font-size:17.5px;line-height:22px}
.label--caps{font-size:18.5px;text-align:center;letter-spacing:.3px}
.dots{position:absolute;border-color:var(--navy);border-style:dotted;border-width:0}
.panel--contact{background:linear-gradient(160deg,#2f2688 0%,#2a2280 55%,#2f2690 100%);color:#fff;text-align:center}
.panel--contact .block{position:absolute;left:24px;right:24px}
.contact-intro{font-size:16px;line-height:19.4px;font-weight:600}
.quote{font-size:15.5px;line-height:19.4px;font-weight:400;color:#e4e2f4}
.will{font-size:15.5px;line-height:19px;font-weight:600}
.will a{color:var(--green);text-decoration:underline}
.contact-head{font-family:"Titillium Web",sans-serif;font-weight:700;font-size:18.5px;text-decoration:underline}
.contact-green{font-family:"Titillium Web",sans-serif;font-weight:700;color:var(--green);font-size:15.5px;line-height:19.5px}
.contact-line{font-family:"Montserrat",sans-serif;font-size:14.4px;line-height:17.8px;color:#fff}
.dot-icon{display:block;margin:0 auto;width:14px;height:14px}
.follow{font-family:"Titillium Web",sans-serif;font-weight:700;font-size:15px;display:flex;justify-content:center;align-items:center;gap:5px}
.follow u{margin-right:4px}
.social{width:15px;height:15px;border-radius:50%;background:var(--green);display:inline-block}
.wordmark{font-family:"Titillium Web",sans-serif;font-weight:700;text-align:center}
.wordmark .name{display:block;font-size:44px;line-height:46px;letter-spacing:1px}
.wordmark .sub{display:block;font-size:11px;letter-spacing:.8px;line-height:14px}
.wordmark--faint{color:var(--mark-grey);width:190px}
.wordmark--faint .name{font-size:24px;line-height:28px;letter-spacing:.5px}
.wordmark--faint .sub{font-size:7.5px;line-height:10px;letter-spacing:.5px}
.cover-title{font-family:"Titillium Web",sans-serif;font-weight:700;font-size:29px;line-height:33px;text-align:center;left:0;right:0}
.cover-sub{font-family:"Titillium Web",sans-serif;font-weight:700;color:var(--navy);font-size:14.5px;line-height:19px;text-align:center;left:0;right:0}
ul.ticks{list-style:none}
ul.ticks li{position:relative;padding-left:17px;margin-bottom:9px}
ul.ticks li svg{position:absolute;left:0;top:3px;width:12px;height:12px}
</style>
</head>
<body>
<svg width="0" height="0" style="position:absolute" aria-hidden="true">
  <defs>
    <symbol id="i-coin" viewBox="0 0 70 70"><circle cx="35" cy="35" r="16" fill="none" stroke="#fff" stroke-width="2"/><path d="M30 26v18M30 26h7a4.5 4.5 0 0 1 0 9h-7m0 0h8a4.5 4.5 0 0 1 0 9h-8" fill="none" stroke="#fff" stroke-width="2"/></symbol>
    <symbol id="i-bank" viewBox="0 0 70 70"><path d="M18 28 35 18l17 10zM19 30h32M21 48h28M18 52h34M23 32v14M29 32v14M35 32v14M41 32v14M47 32v14" fill="none" stroke="#fff" stroke-width="2"/></symbol>
    <symbol id="i-gift" viewBox="0 0 70 70"><path d="M20 30h30v6H20zM22 36h26v16H22zM35 30v22M35 30c-3-6-10-8-10-3 0 3 6 3 10 3 4 0 10 0 10-3 0-5-7-3-10 3" fill="none" stroke="#fff" stroke-width="2"/></symbol>
    <symbol id="i-chart" viewBox="0 0 70 70"><path d="M19 50h33M22 50V40h5v10M31 50V35h5v15M40 50V30h5v20M20 36l12-8 6 4 12-10M46 22h4v4" fill="none" stroke="#fff" stroke-width="2"/></symbol>
    <symbol id="i-calendar" viewBox="0 0 70 70"><path d="M19 24h32v28H19zM19 31h32M25 20v7M45 20v7" fill="none" stroke="#fff" stroke-width="2"/><circle cx="35" cy="27" r="6" fill="#fff"/><path d="M24 37h4v3h-4zM33 37h4v3h-4zM42 37h4v3h-4zM24 44h4v3h-4zM33 44h4v3h-4zM42 44h4v3h-4z" fill="none" stroke="#fff" stroke-width="1.5"/></symbol>
    <symbol id="disc" viewBox="0 0 70 70"><circle cx="35" cy="35" r="33" fill="#2d2484"/><circle cx="35" cy="35" r="30" fill="none" stroke="#fff" stroke-width="1.5"/></symbol>
    <symbol id="ring" viewBox="0 0 86 86"><circle cx="43" cy="43" r="41" fill="#fff" stroke="#3cb83a" stroke-width="4"/><circle cx="43" cy="43" r="34" fill="#2d2484"/></symbol>
  </defs>
</svg>

<main class="stage">
  <section class="sheet sheet--outside">
    <article class="panel panel--impact">
      <div class="photo" role="img" aria-label="Photo of an older man and a young woman smiling at a laptop" style="top:0;height:370px;background:linear-gradient(135deg,#eef0f2 0%,#c9ced8 40%,#8896b8 70%,#cdb7a3 100%)"></div>
      <svg class="curve" style="top:300px;height:75px" viewBox="0 0 385 75" preserveAspectRatio="none"><path d="M0 64Q192-12 385 64V75H0Z" fill="#fff"/><path d="M0 64Q192-12 385 64" fill="none" stroke="var(--green)" stroke-width="7"/></svg>
      <h2 class="abs section-title" style="left:30px;top:364px">THE IMPACT OF YOUR GIFT</h2>
      <p class="abs lead" style="left:30px;top:393px;width:330px">Your generosity drives our mission. With every Smart gift you’re supporting Meadowlark and Allied Services. Join our community of Smart Givers today and make an enduring impact. With Smart Giving your generosity reaches further.  Begin your Smart Giving journey with us today.</p>

      <span class="dots" style="left:63px;top:660px;height:46px;border-left-width:2px"></span>
      <span class="dots" style="left:63px;top:748px;height:46px;border-left-width:2px"></span>
      <span class="dots" style="left:218px;top:660px;height:46px;border-left-width:2px"></span>
      <svg class="icon" style="left:28px;top:593px"><use href="#disc"/><use href="#i-coin"/></svg>
      <span class="label" style="left:107px;top:617px">Crypto</span>
      <svg class="icon" style="left:28px;top:678px"><use href="#disc"/><use href="#i-bank"/></svg>
      <span class="label" style="left:107px;top:702px">DAF’s</span>
      <svg class="icon" style="left:28px;top:762px"><use href="#disc"/><use href="#i-gift"/></svg>
      <span class="label" style="left:107px;top:786px">QCDs</span>
      <svg class="icon" style="left:183px;top:593px"><use href="#disc"/><use href="#i-chart"/></svg>
      <span class="label" style="left:265px;top:607px">Stocks &amp;<br>Securities</span>
      <svg class="icon" style="left:183px;top:678px"><use href="#disc"/><use href="#i-calendar"/></svg>
      <span class="label" style="left:265px;top:692px">Charitable<br>Annuity</span>
      <div class="abs wordmark wordmark--faint" style="left:172px;top:800px"><span class="name">MEADOWLARK</span><span class="sub">AND ALLIED SERVICES, INC.</span></div>
    </article>

    <article class="panel panel--contact">
      <div class="abs" role="img" aria-label="Faint photo of joined hands" style="left:0;top:150px;width:100%;height:200px;background:radial-gradient(ellipse at 50% 50%,rgba(70,60,170,.55),rgba(45,36,132,0) 70%)"></div>
      <p class="block contact-intro" style="top:30px">To learn more about Smart Giving Options and how they can benefit you and Meadowlark and Allied Services, please reach out to our team.  We’re here to help you navigate these giving methods and answer any question you may have.</p>
      <p class="block quote" style="top:162px">Being kind to others is a way of<br>being good to yourself.<br>Miriam Holt</p>
      <p class="block will" style="top:338px">If you do not have a will, go to<br><a>www.WillWise.org.</a><br>In 20 minutes you can have a legal will – for free.</p>
      <div class="block wordmark" style="top:448px;color:#fff"><span class="name">MEADOWLARK</span><span class="sub">AND ALLIED SERVICES, INC.</span></div>
      <p class="block contact-head" style="top:552px">CONTACT US</p>
      <p class="block contact-green" style="top:584px">Have more question? Please contact us at<br>Meadowlark and Allied Services</p>
      <div class="block" style="top:627px">
        <svg class="dot-icon" viewBox="0 0 14 14"><circle cx="7" cy="7" r="7" fill="var(--green)"/><path d="M7 3a2.6 2.6 0 0 0-2.6 2.6C4.4 8 7 11 7 11s2.6-3 2.6-5.4A2.6 2.6 0 0 0 7 3z" fill="var(--indigo)"/></svg>
        <p class="contact-line" style="margin-top:4px">1420 Prairie Rd.<br>Suite 2 Fargo, ND  58102</p>
      </div>
      <div class="block" style="top:685px">
        <svg class="dot-icon" viewBox="0 0 14 14"><circle cx="7" cy="7" r="7" fill="var(--green)"/><path d="M4.5 4c1 0 1.4 1.6 1 2 .6 1.3 1.3 2 2.5 2.5.4-.4 2-.1 2 1-.3 1-1.5 1.3-2.5.8-2-1-3.4-2.4-4-4.3C3.3 5 3.7 4.2 4.5 4z" fill="var(--indigo)"/></svg>
        <p class="contact-line" style="margin-top:6px">701-555-0140 (ext. 100)</p>
      </div>
      <div class="block" style="top:726px">
        <svg class="dot-icon" viewBox="0 0 14 14"><circle cx="7" cy="7" r="7" fill="var(--green)"/><path d="M3.5 4.5h7v5h-7zM3.5 4.5 7 7.3l3.5-2.8" fill="none" stroke="var(--indigo)" stroke-width="1.2"/></svg>
        <p class="contact-line" style="margin-top:6px">jdoe@meadowlarkas.org</p>
      </div>
      <div class="block" style="top:768px">
        <svg class="dot-icon" viewBox="0 0 14 14"><circle cx="7" cy="7" r="7" fill="var(--green)"/><circle cx="7" cy="7" r="3.6" fill="none" stroke="var(--indigo)" stroke-width="1"/><path d="M3.4 7h7.2M7 3.4v7.2" stroke="var(--indigo)" stroke-width="1"/></svg>
        <p class="contact-line" style="margin-top:6px">www.meadowlarkas.org</p>
      </div>
      <p class="block follow" style="top:822px"><u>FOLLOW US:</u><span class="social"></span><span class="social"></span></p>
    </article>

    <article class="panel panel--cover">
      <h1 class="abs cover-title" style="top:20px;color:var(--navy)">Transform Your Giving</h1>
      <p class="abs cover-title" style="top:55px;color:var(--green)">Be Strategic, Be Smart</p>
      <p class="abs cover-sub" style="top:95px">Discover the impact of Smart Giving with<br>Meadowlark and Allied Services</p>
      <div class="photo" role="img" aria-label="Photo of a smiling senior couple embracing" style="top:150px;height:340px;background:linear-gradient(140deg,#f1efec 0%,#e3ddd6 45%,#d2c6ba 100%)"></div>
      <svg class="curve" style="top:142px;height:52px" viewBox="0 0 385 52" preserveAspectRatio="none"><path d="M0 0H385V46Q192-12 0 46Z" fill="#fff"/><path d="M0 46Q192-12 385 46" fill="none" stroke="var(--green)" stroke-width="6"/></svg>
      <svg class="curve" style="top:440px;height:60px" viewBox="0 0 385 60" preserveAspectRatio="none"><path d="M0 56Q192-8 385 56V60H0Z" fill="#fff"/><path d="M0 56Q192-8 385 56" fill="none" stroke="var(--green)" stroke-width="7"/></svg>
      <span class="dots" style="left:111px;top:520px;width:48px;border-top-width:2px"></span>
      <span class="dots" style="left:229px;top:520px;width:44px;border-top-width:2px"></span>
      <span class="dots" style="left:167px;top:621px;width:52px;border-top-width:2px"></span>
      <svg class="icon" style="left:41px;top:486px"><use href="#disc"/><use href="#i-coin"/></svg>
      <svg class="icon" style="left:159px;top:486px"><use href="#disc"/><use href="#i-bank"/></svg>
      <svg class="icon" style="left:273px;top:486px"><use href="#disc"/><use href="#i-gift"/></svg>
      <span class="label label--caps" style="left:26px;top:561px;width:100px">CRYPTO</span>
      <span class="label label--caps" style="left:144px;top:561px;width:100px">DAF’S</span>
      <span class="label label--caps" style="left:258px;top:561px;width:100px">QCDS</span>
      <svg class="icon" style="left:97px;top:587px"><use href="#disc"/><use href="#i-chart"/></svg>
      <svg class="icon" style="left:220px;top:587px"><use href="#disc"/><use href="#i-calendar"/></svg>
      <span class="label label--caps" style="left:72px;top:661px;width:120px">STOCKS &amp;<br>SECURITIES</span>
      <span class="label label--caps" style="left:195px;top:661px;width:120px">CHARITABLE<br>ANNUITY</span>
      <div class="abs wordmark" style="left:0;right:0;top:768px;color:var(--navy)"><span class="name" style="font-size:50px;line-height:54px">MEADOWLARK</span><span class="sub">AND ALLIED SERVICES, INC.</span></div>
    </article>
  </section>

  <section class="sheet sheet--inside">
    <article class="panel">
      <p class="abs body" style="left:30px;top:26px;width:315px;font-size:16.2px;line-height:19.3px;color:#222">We would like to introduce you to five Strategic and Smart ways to give that could potentially be more beneficial to you compared to traditional cash donations. We encourage you to keep this information as a guide for your future contributions.</p>
      <svg class="icon icon--ring" style="left:28px;top:153px"><use href="#ring"/><use href="#i-chart" x="8" y="8" width="70" height="70"/></svg>
      <h3 class="abs item-title" style="left:125px;top:160px">Gifts of Stocks or Appreciated<br>Assets Strategic &amp; Smart</h3>
      <p class="abs item-tag" style="left:125px;top:201px;width:240px">Consider your long-term publicly<br>traded stock as a way to give to<br>your favorite charity.</p>
      <p class="abs body" style="left:30px;top:270px;width:325px">You can make a significantly bigger impact when you donate long-term appreciated securities, including stock, mutual funds, &amp; bonds, directly to your favorite charity.</p>
      <h3 class="abs how" style="left:29px;top:350px">How Does It Work?</h3>
      <p class="abs body" style="left:30px;top:372px;width:325px">When you donate stock to a charity, you will generally take a tax deduction for the full market value. Because you are donating stock, your contribution &amp; tax deduction may be significantly higher than contributing the after-tax proceeds. The same benefits apply when you donate mutual funds or bonds.</p>
      <svg class="icon icon--ring" style="left:28px;top:543px"><use href="#ring"/><use href="#i-bank" x="8" y="8" width="70" height="70"/></svg>
      <h3 class="abs item-title" style="left:125px;top:536px;font-size:16.5px">Donor-Advised Fund (DAF)<br>Strategic &amp; Smart</h3>
      <p class="abs item-tag" style="left:125px;top:582px;width:245px">Consider a DAF – a simple, flexible,<br>and tax-advantageous way to give<br>to your favorite charities.</p>
      <p class="abs body" style="left:30px;top:643px;width:325px;font-size:16px;line-height:19.3px">A Donor-Advised Fund (DAF), is like a charitable investment account for the sole purpose of supporting your favorite charities.</p>
      <h3 class="abs how" style="left:29px;top:718px">How Does It Work?</h3>
      <p class="abs body" style="left:30px;top:740px;width:325px;font-size:14.6px">You establish a DAF &amp; contribute cash, stocks, or non-publicly traded assets, cryptocurrency, &amp; private company stock to be eligible for an immediate tax deduction. Those funds are contributed for tax-free growth. You can recommend grants be made from your DAF to any IRS qualified public charity.</p>
    </article>

    <article class="panel">
      <svg class="icon icon--ring" style="left:28px;top:30px"><use href="#ring"/><use href="#i-gift" x="8" y="8" width="70" height="70"/></svg>
      <h3 class="abs item-title" style="left:127px;top:32px;font-size:15.2px;line-height:19px">Qualified Charitable Distributions<br>(QCDs) Strategic &amp; Smart</h3>
      <p class="abs item-tag" style="left:127px;top:71px;width:245px;font-size:14.8px;line-height:18.5px">Consider a QCD – when planning<br>your IRA withdrawal strategy…<br>&amp; donate to your favorite charity.</p>
      <p class="abs body" style="left:29px;top:133px;width:330px">IRA owners at age 70 ½ or over can transfer dollars from their IRA to charity tax-free each year. These transfers known as Qualified Charitable Distributions (QCDs) offer eligible older Americans a great way to easily give to charity.</p>
      <h3 class="abs how" style="left:29px;top:238px">How Does It Work?</h3>
      <p class="abs body" style="left:29px;top:261px;width:330px">Are you 72 and required to take a minimum distribution (RMD) from your IRA but do not need the funds? Consider a Qualified Charitable Distribution. Normally, distributions from a traditional IRA are taxable when received. With a QCD, these distributions become tax-free when paid directly from the IRA to your favorite eligible charity. An IRA owner wishing to make a QCD should contact their IRA trustee, allowing time to complete the transaction before the end of the year to receive the tax benefit.</p>
      <svg class="icon icon--ring" style="left:28px;top:493px"><use href="#ring"/><use href="#i-calendar" x="8" y="8" width="70" height="70"/></svg>
      <h3 class="abs item-title" style="left:132px;top:494px;font-size:15.2px;line-height:19px">Charitable Gift Annuity<br>Strategic &amp; Smart</h3>
      <p class="abs item-tag" style="left:132px;top:533px;width:200px;font-size:14.8px;line-height:18.5px">Consider establishing a<br>Charitable Gift Annuity</p>
      <p class="abs body" style="left:29px;top:587px;width:330px">You make a donation to a single charity. The gift is set aside in a reserve account and invested.</p>
      <h3 class="abs how" style="left:29px;top:633px">How Does It Work?</h3>
      <p class="abs body" style="left:29px;top:655px;width:330px">A charitable gift annuity is a contract between a donor &amp; a charity. As a donor, you make a sizable gift to charity using cash, securities, or possibly other assets. This money is then invested. In return, you become eligible to take a partial tax deduction for your donation, plus you receive a fixed stream of income from the charity for the rest of your life. At the end of your life (as well as your spouse’s, if you’re giving as a couple), the charity receives the remainder of the gift.</p>
    </article>

    <article class="panel">
      <svg class="icon icon--ring" style="left:27px;top:30px"><use href="#ring"/><use href="#i-coin" x="8" y="8" width="70" height="70"/></svg>
      <h3 class="abs item-title" style="left:130px;top:28px;font-size:17.5px;line-height:22px">Cryptocurrency<br>Strategic &amp; Smart</h3>
      <p class="abs item-tag" style="left:130px;top:77px;width:235px">Consider donating Bitcoin and<br>other cryptocurrencies to your<br>favorite charity.</p>
      <p class="abs body" style="left:28px;top:141px;width:335px;font-size:16.4px;line-height:20px">Bitcoin and other cryptocurrencies can be donated to charity just like other appreciated assets such as stocks and other business interests. Before you sell bitcoin &amp; donate the after-tax proceeds, consider donating your bitcoin directly to a favorite charity.</p>
      <h3 class="abs how" style="left:28px;top:276px">How Does It Work?</h3>
      <p class="abs body" style="left:28px;top:299px;width:335px">Many donors find it useful to open a Donor-Advised Fund (DAF). This strategy includes two significant benefits, both for you and your favorite charity.</p>
      <ul class="abs body ticks" style="left:28px;top:364px;width:310px">
        <li><svg viewBox="0 0 12 12"><circle cx="6" cy="6" r="6" fill="var(--navy)"/><path d="M3.3 6.2 5.2 8 8.8 4.3" fill="none" stroke="#fff" stroke-width="1.5"/></svg>Your tax deduction will be equal to the fair market value of the donated bitcoin (as determined by a qualified appraisal).</li>
        <li><svg viewBox="0 0 12 12"><circle cx="6" cy="6" r="6" fill="var(--navy)"/><path d="M3.3 6.2 5.2 8 8.8 4.3" fill="none" stroke="#fff" stroke-width="1.5"/></svg>Your cryptocurrency donation is tax-smart because it may eliminate capital gains taxes on the value / appreciation AND your favorite charity will receive 100% of the value of the contribution.</li>
      </ul>
      <p class="abs body" style="left:28px;top:526px;width:320px">Often charities are not able to accept direct donations of bitcoin/crypto so using a DAF is a great way to donate these assets.</p>
      <div class="photo" role="img" aria-label="Photo of a senior couple on a park bench with colourful gift bags" style="top:610px;height:256px;background:linear-gradient(160deg,#9fb37a 0%,#6f8f4e 45%,#4f6d36 100%)"></div>
      <svg class="curve" style="top:600px;height:55px" viewBox="0 0 385 55" preserveAspectRatio="none"><path d="M0 0H385V48Q192-10 0 48Z" fill="#fff"/><path d="M0 48Q192-10 385 48" fill="none" stroke="var(--green)" stroke-width="6"/></svg>
    </article>
  </section>
</main>
</body>
</html>
```